Business Card for Industrial Distributor

We need a business card design for an industrial distributor. We sell machine parts for the manufacturing and oil industry. We would like the cards to look clean and modern but with a touch of industry.

Our colors are blue/white.

Please feel free to visit our website www.korvelpartsco.com

Target Market(s)

mexican manufacturers in the automobile/aerospace industry

Industry/Entity Type

Industrial

Colors
ffffff
0555a3

```html
<!DOCTYPE html>
<html lang="en">
<head>
<meta charset="utf-8">
<title>Korvel Business Card</title>
<link href="https://fonts.googleapis.com/css2?family=Montserrat:wght@700&family=Open+Sans:wght@400;600&display=swap" rel="stylesheet">
<style>
  :root {
    --brand-navy: #1f2f8f;
    --brand-blue: #0555a3;
    --card-blue-light: #2a6cc4;
    --card-blue-dark: #1446a0;
    --paper: #ffffff;
    --ink: #222222;
    --stage: #e9ebef;
  }
  * { margin: 0; padding: 0; box-sizing: border-box; }
  html, body {
    width: 1200px;
    height: 900px;
    overflow: hidden;
    background: var(--stage);
    font-family: "Open Sans", Arial, sans-serif;
  }
  .card {
    position: absolute;
    box-shadow: 0 6px 18px rgba(0, 0, 0, 0.18);
  }
  .card--front {
    left: 78px; top: 34px;
    width: 588px; height: 364px;
    background: var(--paper);
  }
  .card--back {
    left: 388px; top: 505px;
    width: 567px; height: 352px;
    background: linear-gradient(160deg, var(--card-blue-light), var(--card-blue-dark));
  }
  .brand {
    position: absolute;
    display: flex;
    align-items: center;
    gap: 14px;
  }
  .brand__dot {
    border-radius: 50%;
    flex: none;
  }
  .brand__name {
    font-family: "Montserrat", Arial, sans-serif;
    font-weight: 700;
    letter-spacing: 0.5px;
    line-height: 1;
  }
  .card--front .brand { left: 86px; top: 88px; }
  .card--front .brand__dot { width: 82px; height: 82px; background: var(--brand-blue); }
  .card--front .brand__name { font-size: 64px; color: var(--brand-navy); }

  .card--back .brand { left: 78px; top: 135px; }
  .card--back .brand__dot { width: 80px; height: 80px; background: var(--paper); }
  .card--back .brand__name { font-size: 62px; color: var(--paper); }

  .person {
    position: absolute;
    right: 308px; top: 216px;
    text-align: right;
    font-size: 15px;
    line-height: 20px;
    color: var(--ink);
  }
  .person__name {
    font-size: 18px;
    font-weight: 600;
    color: var(--brand-blue);
    line-height: 24px;
  }
  .divider {
    position: absolute;
    left: 294px; top: 222px;
    width: 1px; height: 54px;
    background: #9a9a9a;
  }
  .contacts {
    position: absolute;
    left: 306px; top: 218px;
    list-style: none;
    font-size: 15px;
    line-height: 21px;
    color: var(--ink);
  }
  .contacts li { display: flex; align-items: center; gap: 7px; }
  .contacts svg { width: 11px; height: 11px; fill: var(--brand-blue); flex: none; }
  .address {
    position: absolute;
    left: 0; right: 0; top: 296px;
    text-align: center;
    font-size: 15px;
    color: var(--ink);
  }
  .website {
    position: absolute;
    left: 0; right: 0; top: 294px;
    text-align: center;
    font-size: 14px;
    color: var(--paper);
  }
</style>
</head>
<body>
  <section class="card card--front">
    <div class="brand">
      <span class="brand__dot"></span>
      <span class="brand__name">Korvel</span>
    </div>
    <div class="person">
      <div class="person__name">Daniel Reyes</div>
      <div class="person__title">Managing Director</div>
      <div class="person__web">www.websitename.com</div>
    </div>
    <div class="divider"></div>
    <ul class="contacts">
      <li><svg viewBox="0 0 12 12" aria-hidden="true"><path d="M1 4c0-1.5 2-3 5-3s5 1.5 5 3v1H8.5V4h-5v1H1z M2.5 6h7l1 4.5h-9z"/></svg>(044) 123 456 789</li>
      <li><svg viewBox="0 0 12 12" aria-hidden="true"><path d="M3.5 0h5a1 1 0 0 1 1 1v10a1 1 0 0 1-1 1h-5a1 1 0 0 1-1-1V1a1 1 0 0 1 1-1zm.5 1.5v7.5h4V1.5z"/></svg>(044)123456789</li>
      <li><svg viewBox="0 0 12 12" aria-hidden="true"><path d="M0 2h12v8H0z M0.8 2.6 6 6.6l5.2-4v-.6H.8z" fill-rule="evenodd"/></svg>info@youremail.com</li>
    </ul>
    <p class="address">12345,address goes here,country name,12345</p>
  </section>

  <section class="card card--back">
    <div class="brand">
      <span class="brand__dot"></span>
      <span class="brand__name">Korvel</span>
    </div>
    <p class="website">www.korvelpartsco.com</p>
  </section>
</body>
</html>
```